Brindlewick Solutions Ltd

I'd like to create a company letterhead for the attached logo in word format.

I'd like to emphasis the icon in large translucent state from the left corner and ensure that the letterhead colouring matches the colour palette of the current logo with a contrast so it's clear to see. I've attached a copy of our sister company page on the app for reference.

```html
<!DOCTYPE html>
<html lang="en">
<head>
<meta charset="utf-8">
<title>Brindlewick Solutions Ltd — Letterhead</title>
<link rel="stylesheet" href="https://fonts.googleapis.com/css2?family=Montserrat:wght@500&family=Open+Sans:wght@400&display=swap">
<style>
  :root {
    --backdrop: #e6e6e6;
    --paper: #ffffff;
    --brand-teal: #2bb3a3;
    --brand-teal-soft: #dbeeea;
    --fold-grey: #c4c6c6;
    --ink-light: #ffffff;
  }
  * { margin: 0; padding: 0; box-sizing: border-box; }
  html, body {
    width: 1200px;
    height: 800px;
    overflow: hidden;
    background: var(--backdrop);
  }
  .canvas {
    position: relative;
    width: 1200px;
    height: 800px;
    display: flex;
    align-items: center;
    justify-content: center;
  }
  .letterhead {
    position: relative;
    width: 530px;
    height: 750px;
    background: var(--paper);
    overflow: hidden;
    box-shadow: 0 2px 10px rgba(0, 0, 0, 0.08);
  }
  .watermark-disc {
    position: absolute;
    left: -190px;
    top: 150px;
    width: 400px;
    height: 400px;
    border-radius: 50%;
    background: var(--brand-teal-soft);
    opacity: 0.7;
  }
  .footer-band {
    position: absolute;
    inset: 0;
    width: 100%;
    height: 100%;
  }
  .footer-band .band { fill: var(--brand-teal); }
  .footer-band .fold { fill: var(--fold-grey); }
  .brand {
    position: absolute;
    left: 34px;
    top: 30px;
    display: flex;
    flex-direction: column;
    align-items: flex-start;
    gap: 6px;
  }
  .brand-dot {
    width: 26px;
    height: 26px;
    border-radius: 50%;
    background: var(--brand-teal);
    margin-left: 4px;
  }
  .brand-name {
    font-family: "Montserrat", sans-serif;
    font-weight: 500;
    font-size: 17px;
    color: var(--brand-teal);
    letter-spacing: 0.2px;
  }
  .website {
    position: absolute;
    right: 26px;
    top: 30px;
    font-family: "Open Sans", sans-serif;
    font-size: 8.5px;
    color: var(--brand-teal);
  }
  .contact {
    position: absolute;
    right: 22px;
    top: 658px;
    list-style: none;
    font-family: "Open Sans", sans-serif;
    font-size: 9px;
    color: var(--ink-light);
    text-align: right;
  }
  .contact li {
    display: flex;
    justify-content: flex-end;
    align-items: center;
    gap: 5px;
    height: 17px;
    white-space: nowrap;
  }
  .contact-icon {
    width: 11px;
    height: 11px;
    flex: none;
  }
  .contact-icon circle { fill: var(--ink-light); }
  .contact-icon path { fill: none; stroke: var(--brand-teal); stroke-width: 1.2; stroke-linecap: round; stroke-linejoin: round; }
</style>
</head>
<body>
<main class="canvas">
  <article class="letterhead">
    <div class="watermark-disc" aria-hidden="true"></div>

    <svg class="footer-band" viewBox="0 0 530 750" aria-hidden="true">
      <polygon class="fold" points="0,647 330,682 530,537 530,545 330,690 0,655"/>
      <polygon class="band" points="0,655 330,690 530,545 530,750 0,750"/>
    </svg>

    <header class="brand">
      <span class="brand-dot" aria-hidden="true"></span>
      <span class="brand-name">Brindlewick Solutions Ltd</span>
    </header>

    <p class="website">www.brindlewicksolutions.com</p>

    <ul class="contact">
      <li>(00) 04512 338 760
        <svg class="contact-icon" viewBox="0 0 12 12" aria-label="Phone"><circle cx="6" cy="6" r="6"/><path d="M4 3.2 L5 4.6 L4.5 5.4 Q5.4 6.9 6.6 7.5 L7.4 7 L8.8 8 L8.2 9 Q5 8.6 3.1 4 Z"/></svg>
      </li>
      <li>hello@brindlewick.com
        <svg class="contact-icon" viewBox="0 0 12 12" aria-label="Email"><circle cx="6" cy="6" r="6"/><path d="M3 4 H9 V8 H3 Z M3 4 L6 6.3 L9 4"/></svg>
      </li>
      <li>Unit 7 Harlow Yard, Kenmore 4820
        <svg class="contact-icon" viewBox="0 0 12 12" aria-label="Address"><circle cx="6" cy="6" r="6"/><path d="M6 9.4 Q3.6 6.6 3.8 5 A2.2 2.2 0 0 1 8.2 5 Q8.4 6.6 6 9.4 Z"/></svg>
      </li>
    </ul>
  </article>
</main>
</body>
</html>
```